BOLD & MINIMALIST DESIGN NEEDED

We want a very bold but minimalistic business card design that is impactful and utilizes both sides of the business card. Our current logo is included for your use.

We want bold fonts and good use of negative space. We don't want the logo to overpower the design.

Target Market(s)

Professionals who are building new commercial buildings.

Industry/Entity Type

Construction

Contact Information for Business Card

Name, Title, email, office phone, cell phone, website

Font styles to use
Serif
Sans Serif

Requirements
Must have
• Bold design!

```html
<!DOCTYPE html>
<html lang="en">
<head>
<meta charset="utf-8">
<title>Ridgeline Design + Build — Business Card</title>
<link href="https://fonts.googleapis.com/css2?family=Oswald:wght@500;600&family=Montserrat:wght@400;500&display=swap" rel="stylesheet">
<style>
  :root{
    --stage:#141414;
    --card-white:#ffffff;
    --card-dark:#2a2a2a;
    --card-dark-deep:#1c1c1c;
    --ink:#111111;
    --green:#7dc21e;
    --text-light:#f2f2f2;
    --shade-mid:#3a3a3a;
  }
  *{box-sizing:border-box;margin:0;padding:0}
  html,body{width:1200px;height:897px;overflow:hidden;background:var(--stage)}
  .canvas{position:relative;width:1200px;height:897px}
  .card{position:absolute;left:303px;width:594px;height:338px;border-radius:18px;overflow:hidden}
  .card--front{top:92px;background:var(--card-white)}
  .card--back{top:469px;background:var(--card-dark-deep)}

  .brand{position:absolute;left:0;right:0;top:66px;text-align:center}
  .brand__name{font-family:"Oswald",sans-serif;font-weight:600;font-size:40px;letter-spacing:1px;color:var(--ink);line-height:1}
  .brand__tag{font-family:"Oswald",sans-serif;font-weight:600;font-size:13px;letter-spacing:5px;color:var(--ink);margin-top:6px}

  .front-band{position:absolute;left:0;top:0;width:594px;height:338px}

  .contact{position:absolute;left:34px;top:240px;list-style:none;font-family:"Montserrat",sans-serif;font-size:14px;color:var(--text-light);line-height:18px}
  .contact li{display:flex;align-items:center;gap:6px}
  .contact svg{width:13px;height:13px;flex:none}
  .contact .accent{color:var(--green)}

  .person{position:absolute;right:34px;top:248px;text-align:right}
  .person__name{font-family:"Oswald",sans-serif;font-weight:600;font-size:31px;color:var(--green);line-height:1;letter-spacing:.3px}
  .person__title{font-family:"Montserrat",sans-serif;font-size:14px;color:var(--text-light);margin-top:5px;letter-spacing:.5px}

  .back-pattern{position:absolute;inset:0;background:linear-gradient(120deg,#161616 0%,#262626 45%,#4a4a4a 100%)}
  .back-brand{position:absolute;left:0;right:0;top:172px;text-align:center;font-family:"Oswald",sans-serif;font-weight:600;font-size:26px;letter-spacing:2px;color:var(--text-light)}
</style>
</head>
<body>
<main class="canvas">
  <section class="card card--front" aria-label="Card front">
    <svg class="front-band" viewBox="0 0 594 338" aria-hidden="true">
      <path d="M0 222 Q297 150 594 222 L594 338 L0 338 Z" fill="var(--card-dark)"/>
      <path d="M0 222 Q297 140 594 220" fill="none" stroke="var(--green)" stroke-width="5"/>
    </svg>
    <div class="brand">
      <div class="brand__name">RIDGELINE</div>
      <div class="brand__tag">DESIGN + BUILD</div>
    </div>
    <ul class="contact">
      <li><svg viewBox="0 0 24 24"><path fill="var(--green)" d="M6.6 10.8a15 15 0 0 0 6.6 6.6l2.2-2.2c.3-.3.7-.4 1-.2 1.1.4 2.3.6 3.6.6.6 0 1 .4 1 1V20c0 .6-.4 1-1 1A17 17 0 0 1 3 4c0-.6.4-1 1-1h3.5c.6 0 1 .4 1 1 0 1.3.2 2.5.6 3.6.1.3 0 .7-.2 1z"/></svg>(555) 014-2387</li>
      <li><svg viewBox="0 0 24 24"><path fill="var(--green)" d="M3 9c2-4 16-4 18 0l-3 2-2-2H8L6 11zM6 12h12l2 8H4z"/></svg>(555) 014-2387</li>
      <li><svg viewBox="0 0 24 24"><rect x="2.5" y="5" width="19" height="14" rx="1.5" fill="none" stroke="var(--green)" stroke-width="2"/><path d="M3 6l9 7 9-7" fill="none" stroke="var(--green)" stroke-width="2"/></svg>ridgelinebuild@mail.com</li>
      <li><svg viewBox="0 0 24 24"><g fill="none" stroke="var(--green)" stroke-width="1.8"><circle cx="12" cy="12" r="9"/><ellipse cx="12" cy="12" rx="4" ry="9"/><path d="M3 12h18M5 7h14M5 17h14"/></g></svg>www.<span class="accent">ridgelinebuild</span>.com</li>
    </ul>
    <div class="person">
      <div class="person__name">MARCUS HALE</div>
      <div class="person__title">OWNER</div>
    </div>
  </section>

  <section class="card card--back" aria-label="Card back">
    <div class="back-pattern" role="img" aria-label="Repeating embossed brand pattern in dark greys"></div>
    <div class="back-brand">RIDGELINE</div>
  </section>
</main>
</body>
</html>
```